Website Design for The Elder Nook

Please design and code a new website.
Here are the sites I like best:
http://www.voyaglint.com/alternate/
http://www.wheelgiftbay.org
Please make it similar but look at the competitor site (below) for images and wording. This is NOT a car donation site. It's a senior lead placement site like https://www.kinhavenfinder.com. I just like this sites above as a lead generation sites.
Competitor site:
https://www.kinhavenfinder.com (use ideas / verbiage from this site)
Updates
Competitor site:
Coding
Coded - Design and coding required
Number of Pages Required
1 page
Look and feel
Each slider illustrates characteristics of the customer's brand and the style your logo design should communicate.

```html
<!DOCTYPE html>
<html lang="en">
<head>
<meta charset="utf-8">
<title>The Elder Nook — Senior Living Advisors</title>
<link href="https://fonts.googleapis.com/css2?family=Roboto:ital,wght@0,300;0,400;0,500;0,700;1,300;1,400;1,500&family=Oswald:wght@500&display=swap" rel="stylesheet">
<style>
:root{
  --green:#1a9a4a;
  --green-dark:#0e8a44;
  --lime:#7dbb2e;
  --navy:#0d2f7f;
  --ink:#333;
  --muted:#555;
  --page:#f1f1f1;
  --panel:#eef2f0;
  --white:#fff;
}
*{box-sizing:border-box;margin:0;padding:0}
html,body{width:1200px;height:3342px;overflow:hidden}
body{background:var(--page);font-family:Roboto,sans-serif;color:var(--ink);position:relative}
.site{position:absolute;left:83px;top:0;width:1034px;height:3342px;background:var(--white);overflow:hidden}
.abs{position:absolute}
.center{text-align:center}

/* header */
.brand{left:92px;top:30px;display:flex;align-items:center;gap:12px}
.brand-dot{width:40px;height:40px;border-radius:50%;background:var(--lime)}
.brand-name{font-size:30px;font-weight:400;color:var(--green)}
.call{left:515px;top:36px;text-align:right;width:155px}
.call small{display:block;font-size:18px;color:#444}
.call b{font-size:22px;color:#222;font-weight:700}
.call-ico{left:684px;top:42px;width:40px;height:40px;border:2px solid var(--green);border-radius:50%}
.estimate{left:745px;top:42px;width:204px;height:40px;border:2px solid var(--navy);border-radius:22px;color:var(--navy);font-weight:700;font-size:15px;line-height:36px;text-align:center}
.nav{top:122px;left:0;width:1034px;height:48px;background:var(--navy);display:flex;align-items:center;padding-left:92px;gap:34px}
.nav a{color:#fff;font-size:14.5px;font-weight:500;text-decoration:none}

/* hero */
.hero{top:170px;left:0;width:1034px;height:535px;background:linear-gradient(100deg,#4f6a4a 0%,#8aa07a 35%,#c9bba6 60%,#8e7f6b 100%)}
.form-panel{left:31px;top:88px;width:339px;height:379px;background:rgba(40,40,40,.85);padding:22px 22px}
.form-panel h2{color:#fff;font-size:24px;font-weight:500;margin-bottom:14px}
.field{height:34px;background:#fafafa;border:1px solid #ccc;border-radius:2px;margin-bottom:11px;font-size:11px;padding:0 11px;line-height:32px;color:#555}
.btn-green{background:var(--lime);color:#fff;font-weight:500;text-align:center}
.form-panel .btn-green{height:44px;line-height:44px;font-size:17px;margin-top:4px}
.dots{left:55px;top:447px;display:flex;gap:8px}
.dots i{width:16px;height:16px;border:1.5px solid #bbb;border-radius:50%}
.dots i:first-child{background:#222}
.hero-title{left:395px;top:342px;font-family:Oswald,sans-serif;font-size:36px;line-height:49px;color:#fff;text-transform:uppercase;letter-spacing:-.5px}

/* support */
.lead{top:767px;left:0;width:1034px;font-size:29px;font-style:italic;font-weight:300;color:#222}
.lead b{font-style:normal;font-weight:700}
.intro{top:822px;left:140px;width:754px;font-size:14px;line-height:25px;color:#444}
.feature{top:905px;width:170px;text-align:center;font-size:15px;line-height:22px;color:#333}
.ring{width:72px;height:72px;border:2px solid var(--green);border-radius:50%;margin:0 auto 14px;display:flex;align-items:center;justify-content:center}

/* services */
.services{top:1127px;left:0;width:1034px;height:600px;background:var(--panel)}
.sec-title{font-size:34px;font-weight:300;font-style:italic;color:#222}
.sec-title b{font-style:normal;font-weight:700}
.rule{width:80px;height:3px;background:var(--green);margin:0 auto}
.card{background:#fff;width:275px;height:320px;box-shadow:0 2px 4px rgba(0,0,0,.08);text-align:center}
.card .photo{height:190px;border-bottom:3px solid var(--lime)}
.card h3{font-size:17px;font-weight:500;margin:14px 0 10px}
.card p{font-size:12.5px;line-height:22.5px;color:#444;padding:0 14px}

/* advisor */
.advisor{top:1713px;left:0;width:1034px;height:460px;background:linear-gradient(180deg,#138f45,#1a9a4a 60%,#189847)}
.advisor h2{top:130px;width:1034px;color:#fff;font-size:30px;font-style:italic;font-weight:300}
.advisor h2 b{font-style:normal;font-weight:700}
.advisor .sub{top:190px;width:1034px;color:#fff;font-size:15px}
.ticks{left:180px;top:255px;color:#fff;font-size:15.5px;list-style:none}
.ticks li{height:38px;display:flex;align-items:center;gap:10px}
.search{left:498px;top:254px;width:374px;height:44px;background:#fff;font-size:13px;color:#666;padding-left:21px;line-height:44px}
.advisor .btn-green{left:498px;top:313px;width:374px;height:45px;line-height:45px;font-size:16px;letter-spacing:.5px}

/* testimonials */
.quote{background:#fafafa;border:1px solid #e6e6e6;width:276px;height:205px;text-align:center;padding-top:60px}
.quote.raised{background:#fff;box-shadow:0 4px 10px rgba(0,0,0,.12)}
.quote p{font-size:12.5px;line-height:22.5px;color:#555;padding:0 22px}
.quote cite{display:block;margin-top:10px;color:#2d5fb2;font-size:13px;font-style:italic}
.avatar{width:90px;height:90px;border-radius:50%;border:3px solid #f1f1f1;background:linear-gradient(135deg,#b9a48f,#6e5c4d)}

/* footer */
.footer{top:2740px;left:0;width:1034px;height:602px}
.footer-bg{top:42px;left:0;width:1034px;height:560px;background:linear-gradient(160deg,#159447 0%,#0b6f62 50%,#0d3a82 100%)}
.footer h4{color:#fff;font-size:22px;font-weight:700}
.footer .bar{width:58px;height:2px;background:#fff;margin-top:24px}
.f-field{left:91px;width:339px;height:32px;border:1px solid #fff;color:#fff;font-size:10px;padding:0 11px;line-height:30px}
.f-submit{left:91px;top:415px;width:166px;height:34px;background:#111;color:#fff;font-size:14px;font-weight:700;text-align:center;line-height:34px}
.c-item{left:500px;display:flex;gap:16px;color:#fff;font-size:13.5px;line-height:22px}
.c-ico{width:30px;height:30px;border:1.5px solid #fff;border-radius:50%;flex:none;display:flex;align-items:center;justify-content:center}
.links{left:800px;top:210px;list-style:none;color:#fff;font-size:13.5px;line-height:26px}
.social{left:506px;top:420px;display:flex;gap:5px}
.social i{width:29px;height:29px;border:1.5px solid #fff;border-radius:50%}
.f-line{left:0;top:500px;width:1034px;height:1px;background:rgba(255,255,255,.25)}
.copy{top:540px;width:1034px;color:#fff;font-size:13.5px}
</style>
</head>
<body>
<div class="site">

  <!-- header -->
  <div class="abs brand"><span class="brand-dot"></span><span class="brand-name">The Elder Nook</span></div>
  <div class="abs call"><small>Call Us</small><b>555 0142 7788</b></div>
  <div class="abs call-ico">
    <svg width="36" height="36" viewBox="0 0 36 36"><path d="M12 10c1-1 2-1 3 0l2 3c.5 1 .3 1.8-.5 2.4l-1 .8c1 2.3 2.8 4.1 5 5l.8-1c.6-.8 1.5-1 2.4-.5l3 2c1 1 1 2 0 3l-1.3 1.3c-1.5 1.5-5 .5-8.5-3s-4.6-7-3.1-8.6z" fill="#1a9a4a"/></svg>
  </div>
  <div class="abs estimate">GET A FREE ESTIMATE!</div>

  <nav class="abs nav">
    <a>HOME</a><a>ASSISTED LIVING</a><a>MEMORY CARE</a><a>NURSING HOMES</a><a>PLANNING &amp; ADVICE</a><a>BLOG</a><a>CONTACT US</a>
  </nav>

  <!-- hero -->
  <section class="abs hero" role="img" aria-label="Caregiver smiling beside a senior man outdoors">
    <div class="abs form-panel">
      <h2>CONTACT FORM</h2>
      <div class="field">First Name</div>
      <div class="field">Last Name</div>
      <div class="field">Zip Code</div>
      <div class="field">Day Phone</div>
      <div class="field">Email Address</div>
      <div class="btn-green">SUBMIT</div>
    </div>
    <div class="abs dots"><i></i><i></i><i></i></div>
    <svg class="abs" style="left:410px;top:250px" width="80" height="80" viewBox="0 0 80 80"><path d="M70 78C66 40 40 20 8 16" stroke="#fff" stroke-width="3" fill="none"/><path d="M8 16l22-8M8 16l18 14" stroke="#fff" stroke-width="3" fill="none"/></svg>
    <div class="abs hero-title">You know your family.<br>We know senior living.</div>
  </section>

  <!-- support -->
  <h2 class="abs lead center">The support you need to make <b>THE RIGHT CHOICE</b></h2>
  <p class="abs intro center">Sed ut perspiciatis unde omnis iste natus error sit voluptatem accusantium doloremque laudantium, totam rem aperiam, eaque ipsa quae ab illo inventore veritatis et quasi architecto beatae vitae dicta</p>

  <div class="abs feature" style="left:72px"><div class="ring"><svg width="36" height="36" viewBox="0 0 36 36"><rect x="4" y="6" width="24" height="24" rx="3" fill="none" stroke="#1a9a4a" stroke-width="3"/><path d="M10 17l6 6 14-15" stroke="#1a9a4a" stroke-width="4" fill="none"/></svg></div>Dedicated local<br>advisor</div>
  <div class="abs feature" style="left:252px"><div class="ring"><svg width="36" height="36" viewBox="0 0 36 36"><path d="M18 5L3 18h4v12h8v-8h6v8h8V18h4z" fill="#1a9a4a"/></svg></div>Hand-picked list of communities to match your needs</div>
  <div class="abs feature" style="left:432px"><div class="ring"><svg width="40" height="40" viewBox="0 0 40 40"><circle cx="22" cy="12" r="8" fill="none" stroke="#1a9a4a" stroke-width="2"/><text x="22" y="16" font-size="11" text-anchor="middle" fill="#1a9a4a" font-family="Roboto">$</text><path d="M4 30h8l6 3h10l8-7-3-2-8 4h-8" fill="none" stroke="#1a9a4a" stroke-width="2"/></svg></div>Full details and<br>pricing</div>
  <div class="abs feature" style="left:611px"><div class="ring"><svg width="36" height="36" viewBox="0 0 36 36"><rect x="5" y="8" width="26" height="23" rx="2" fill="none" stroke="#1a9a4a" stroke-width="2.5"/><rect x="5" y="8" width="26" height="6" fill="#1a9a4a"/><path d="M10 19h4M16 19h4M22 19h4M10 25h4M16 25h4M22 25h4" stroke="#1a9a4a" stroke-width="3"/></svg></div>Help scheduling<br>tours</div>
  <div class="abs feature" style="left:791px"><div class="ring"><svg width="36" height="36" viewBox="0 0 36 36"><rect x="8" y="5" width="20" height="26" rx="2" fill="none" stroke="#1a9a4a" stroke-width="2"/><path d="M12 20h12M12 24h12M12 28h8" stroke="#1a9a4a" stroke-width="2"/><circle cx="18" cy="12" r="3" fill="#1a9a4a"/></svg></div>Move in support</div>

  <!-- services -->
  <section class="abs services">
    <h2 class="abs sec-title center" style="top:75px;width:1034px">OUR <b>SERVICES</b></h2>
    <div class="abs rule" style="top:138px;left:477px"></div>
    <article class="abs card" style="left:80px;top:178px"><div class="photo" role="img" aria-label="Nurse chatting with a senior couple on a sofa" style="background:linear-gradient(135deg,#c9a890,#7d6a8c)"></div><h3>ASSISTED LIVING</h3><p>Sed ut perspiciatis unde omnis iste natus error sit voluptatem accusantium loremque laudantium, totam rem aperiam</p></article>
    <article class="abs card" style="left:380px;top:208px"><div class="photo" role="img" aria-label="Young woman showing a tablet to a senior woman" style="background:linear-gradient(135deg,#d8d2c8,#9c8a7e)"></div><h3>MEMORY CARE</h3><p>Sed ut perspiciatis unde omnis iste natus error sit voluptatem accusantium loremque laudantium, totam rem aperiam</p></article>
    <article class="abs card" style="left:678px;top:178px"><div class="photo" role="img" aria-label="Nurse in blue uniform playing a board game with a senior man" style="background:linear-gradient(135deg,#7f9cc4,#3a63b0)"></div><h3>NURSING HOMES</h3><p>Sed ut perspiciatis unde omnis iste natus error sit voluptatem accusantium loremque laudantium, totam rem aperiam</p></article>
  </section>

  <!-- advisor -->
  <section class="abs advisor">
    <svg class="abs" style="left:0;top:0" width="1034" height="70" viewBox="0 0 1034 70"><path d="M0 0h1034v0C900 40 700 60 517 60S134 40 0 0z" fill="#eef2f0"/><path d="M70 8C250 50 400 62 517 62S784 50 964 8" stroke="#7dbb2e" stroke-width="4" fill="none"/></svg>
    <h2 class="abs center">Your <b>LOCAL ADVISOR</b> INFORMS. YOU DECIDE.</h2>
    <p class="abs sub center">Over 400 senior advisors across the U.S. and Canada are ready to help your family with:</p>
    <ul class="abs ticks">
      <li><svg width="14" height="14" viewBox="0 0 14 14"><circle cx="7" cy="7" r="6" fill="none" stroke="#fff" stroke-width="1.5"/><path d="M4 7h6M7.5 4.5L10 7 7.5 9.5" stroke="#fff" stroke-width="1.5" fill="none"/></svg>Insider's tips for the area near you</li>
      <li><svg width="14" height="14" viewBox="0 0 14 14"><circle cx="7" cy="7" r="6" fill="none" stroke="#fff" stroke-width="1.5"/><path d="M4 7h6M7.5 4.5L10 7 7.5 9.5" stroke="#fff" stroke-width="1.5" fill="none"/></svg>Advice tailored to your unique situation</li>
      <li><svg width="14" height="14" viewBox="0 0 14 14"><circle cx="7" cy="7" r="6" fill="none" stroke="#fff" stroke-width="1.5"/><path d="M4 7h6M7.5 4.5L10 7 7.5 9.5" stroke="#fff" stroke-width="1.5" fill="none"/></svg>Time saving know-how and resources</li>
    </ul>
    <div class="abs search">Enter city or postal code</div>
    <div class="abs btn-green">START YOUR SEARCH</div>
  </section>

  <!-- testimonials -->
  <h2 class="abs center" style="top:2237px;width:1034px;font-size:32px;font-weight:300;font-style:italic;color:#222"><b style="font-style:normal;font-weight:700">98%</b> of our customers recommend our service</h2>
  <div class="abs rule" style="top:2309px;left:476px"></div>

  <div class="abs quote" style="left:91px;top:2421px"><p>Sed ut perspiciatis unde omnis iste natus error sit voluptatem accusantium doloremque laudantium, totam rem aperiam, eaque ipsa quae ab</p><cite>Delmar, R.</cite></div>
  <div class="abs quote raised" style="left:380px;top:2421px"><p>Sed ut perspiciatis unde omnis iste natus error sit voluptatem accusantium doloremque laudantium, totam rem aperiam, eaque ipsa quae ab</p><cite>Delmar, R.</cite></div>
  <div class="abs quote" style="left:668px;top:2421px"><p>Sed ut perspiciatis unde omnis iste natus error sit voluptatem accusantium doloremque laudantium, totam rem aperiam, eaque ipsa quae ab</p><cite>Delmar, R.</cite></div>
  <div class="abs avatar" style="left:184px;top:2371px" role="img" aria-label="Portrait of a senior man"></div>
  <div class="abs avatar" style="left:472px;top:2371px" role="img" aria-label="Portrait of a smiling senior couple"></div>
  <div class="abs avatar" style="left:760px;top:2371px" role="img" aria-label="Portrait of a senior woman with her father"></div>

  <!-- footer -->
  <footer class="abs footer">
    <svg class="abs" style="left:0;top:0" width="1034" height="44" viewBox="0 0 1034 44"><path d="M297 44C320 10 345 0 390 0h254c45 0 70 10 93 44z" fill="#12804f"/></svg>
    <div class="abs footer-bg"></div>
    <div class="abs" style="top:58px;width:1034px;display:flex;justify-content:center;align-items:center;gap:10px">
      <span style="width:30px;height:30px;border-radius:50%;background:#fff"></span>
      <span style="color:#fff;font-size:26px">The Elder Nook</span>
    </div>

    <h4 class="abs" style="left:89px;top:128px">E-MAIL US<div class="bar"></div></h4>
    <h4 class="abs" style="left:500px;top:128px">CONTACT US<div class="bar"></div></h4>
    <h4 class="abs" style="left:800px;top:128px">QUICK LINKS<div class="bar"></div></h4>

    <div class="abs f-field" style="top:214px">First Name</div>
    <div class="abs f-field" style="top:256px">Email Address</div>
    <div class="abs f-field" style="top:298px">Phone Number</div>
    <div class="abs f-field" style="top:340px;height:56px">Message :</div>
    <div class="abs f-submit">SUBMIT</div>

    <div class="abs c-item" style="top:212px"><span class="c-ico"><svg width="14" height="16" viewBox="0 0 14 16"><path d="M7 1a5 5 0 0 1 5 5c0 4-5 9-5 9S2 10 2 6a5 5 0 0 1 5-5z" fill="none" stroke="#fff" stroke-width="1.5"/><circle cx="7" cy="6" r="1.8" fill="#fff"/></svg></span><span>42 Nookside Lane<br>Suite 300<br>Harbor City, Florida 30000</span></div>
    <div class="abs c-item" style="top:290px"><span class="c-ico"><svg width="16" height="16" viewBox="0 0 36 36"><path d="M9 6c1-1 2-1 3 0l3 4c.5 1 .3 1.8-.5 2.4l-1.5 1c1 3 4 6.5 7 7.5l1-1.5c.6-.8 1.5-1 2.4-.5l4 3c1 1 1 2 0 3l-2 2c-2 2-7 .5-12-4.5S5 12 7 8z" fill="#fff"/></svg></span><span>Phone:<br>555 0142 7788</span></div>
    <div class="abs c-item" style="top:348px"><span class="c-ico"><svg width="14" height="12" viewBox="0 0 14 12"><rect x="1" y="1" width="12" height="10" fill="none" stroke="#fff" stroke-width="1.3"/><path d="M1 1l6 5 6-5" fill="none" stroke="#fff" stroke-width="1.3"/></svg></span><span>Email:<br>hello@theeldernook.com</span></div>
    <div class="abs social"><i></i><i></i><i></i><i></i></div>

    <ul class="abs links"><li>Home</li><li>About</li><li>Assisted Living</li><li>Memory Care</li><li>Nursing Homes</li><li>Planning &amp; Advice</li><li>Contact Us</li></ul>

    <div class="abs f-line"></div>
    <p class="abs copy center">Copyright © 2019 The Elder Nook. Privacy Policy. All Rights Reserved.</p>
  </footer>
</div>
</body>
</html>
```